Organization and people consulting firm needs a website design

I need a website that promotes and explains the consulting service we will provide. The organization is called Bluefinch Advisory Partners. Our services include organization design, employee experience, change management, and executive coaching. I would like to see a simple clean and professional design, that reflects a modern and forward looking professional services company

Target Market(s)

Mid market and large companies

Industry/Entity Type

Management Consulting

Coding

Coded - Design and coding required

Number of Pages Required

5+ page

Font styles to use
Sans Serif

Colors

Designer to choose colors to be used in the design.

Requirements
Must have
• The following pages: Home, The Way We Work, What We Do, Our Founder, Insights, Contact.
• Search button.
• Hyper links (will be provided with main body text)
• Scrolling website with summaries at top level and links to more detail at lower level (like this website: veltracore.com)
• Company logo (uploaded)
• I have text for each of the pages that I can upload once the basic design is done
Should not have
• No clutter, keep the design clean

```html
<!DOCTYPE html>
<html lang="en">
<head>
<meta charset="utf-8">
<title>Bluefinch Advisory Partners</title>
<link href="https://fonts.googleapis.com/css2?family=Open+Sans:wght@400;600;700&display=swap" rel="stylesheet">
<style>
:root{
  --red:#d7092f;
  --ink:#2a2a2a;
  --text:#444;
  --muted:#777;
  --grey:#f3f3f3;
  --card:#f1f1f1;
  --line:#cfcfcf;
  --dark:#2d2d2d;
  --white:#fff;
}
*{box-sizing:border-box;margin:0;padding:0}
html,body{width:1200px;height:3321px;overflow:hidden}
body{position:relative;background:var(--white);font-family:"Open Sans",Arial,sans-serif;color:var(--text)}
.abs{position:absolute}
.section-bg{position:absolute;left:0;width:1200px}
h2.title{position:absolute;font-size:32px;font-weight:600;color:var(--red);line-height:1}
.center{left:0;width:1200px;text-align:center}
.btn{position:absolute;display:flex;align-items:center;justify-content:center;background:var(--red);color:var(--white);font-size:13px;text-decoration:none}
.btn-ghost{position:absolute;display:flex;align-items:center;justify-content:center;border:1px solid var(--line);background:var(--white);color:var(--muted);font-size:11px;text-decoration:none}

/* header */
.hero{position:absolute;left:0;top:0;width:1200px;height:615px;overflow:hidden}
.brand{position:absolute;left:133px;top:30px;display:flex;align-items:center;gap:12px;color:var(--red);font-size:26px;font-weight:600;text-decoration:none}
.brand-mark{width:26px;height:26px;background:var(--red)}
.search{position:absolute;left:1014px;top:31px;width:53px;height:53px;background:var(--red);display:flex;align-items:center;justify-content:center}
.nav{position:absolute;left:0;top:569px;width:1200px;height:46px;background:linear-gradient(90deg,rgba(25,25,25,0) 0%,rgba(25,25,25,.88) 22%,rgba(25,25,25,.92) 100%)}
.nav a{position:absolute;top:15px;font-size:13px;font-weight:700;color:var(--white);text-decoration:none;text-transform:uppercase;transform:translateX(-50%);white-space:nowrap}
.nav a.active{color:var(--red)}

/* way we work */
.intro-text{position:absolute;left:133px;top:768px;width:552px;font-size:13.5px;line-height:24px;color:var(--text)}
.intro-list{position:absolute;left:133px;top:870px;list-style:none;font-size:13.5px;line-height:29px}
.intro-list li::before{content:"•";margin-right:9px}
.photo{position:absolute}

/* cards */
.service{position:absolute;top:1289px;width:217px;height:305px;background:var(--card);text-align:center}
.service-icon{height:113px;background:var(--red);display:flex;align-items:center;justify-content:center}
.service h3{margin-top:18px;font-size:19px;font-weight:600;line-height:24px;color:var(--red)}
.service p,.insight p{margin:12px auto 0;width:196px;font-size:10.5px;line-height:15px;color:var(--text)}
.service .btn-ghost,.insight .btn-ghost{left:70px;width:77px;height:27px}
.service .btn-ghost{top:254px}

/* founder */
.founder-name{position:absolute;right:133px;top:1847px;font-size:22px;font-weight:600;color:var(--ink)}
.founder-text{position:absolute;left:510px;top:1886px;width:557px;text-align:right;font-size:13.5px;line-height:24px}

/* insights */
.insight{position:absolute;top:2380px;width:217px;height:210px;background:var(--card);text-align:center}
.date{position:absolute;left:50%;top:0;transform:translateX(-50%);width:102px;height:25px;background:var(--red);color:var(--white);font-size:12px;font-weight:700;display:flex;align-items:center;justify-content:center}
.insight h3{padding-top:40px;width:205px;margin:0 auto;font-size:14.5px;font-weight:700;line-height:21px;color:var(--ink)}
.insight p{margin-top:10px}
.insight .btn-ghost{top:158px}

/* contact */
.field{position:absolute;height:38px;border:1px solid var(--line);background:var(--white);font-size:11px;color:#555;padding:11px 12px}
.map-info{position:absolute;left:746px;top:3011px;width:321px;height:95px;background:var(--red);color:var(--white);font-size:14px;line-height:25px;text-align:center;padding-top:10px}

/* footer */
.footer-links{position:absolute;left:133px;top:3231px;font-size:11px;color:#ddd;word-spacing:2px}
.footer-links span{margin:0 8px;color:#aaa}
.copyright{position:absolute;left:133px;top:3260px;font-size:11px;color:#bbb}
.social{position:absolute;top:3244px;width:24px;height:24px;border-radius:50%}
</style>
</head>
<body>

<header class="hero">
  <svg class="abs" width="1200" height="615" style="left:0;top:0">
    <defs>
      <linearGradient id="heroTone" x1="0" y1="0" x2="1" y2="1">
        <stop offset="0" stop-color="#9a8f86"/>
        <stop offset="0.45" stop-color="#b9a9a0"/>
        <stop offset="0.7" stop-color="#7b5b57"/>
        <stop offset="1" stop-color="#3b3433"/>
      </linearGradient>
    </defs>
    <rect role="img" aria-label="Photo of a team of colleagues laughing together in a modern office" width="1200" height="615" fill="url(#heroTone)"/>
    <path d="M0 0 H700 C420 40 150 250 0 560 Z" fill="#fff"/>
  </svg>
  <a class="brand" href="#"><span class="brand-mark"></span>Bluefinch Advisory Partners</a>
  <a class="search" href="#" aria-label="Search">
    <svg width="24" height="24" viewBox="0 0 24 24"><circle cx="10" cy="10" r="7" fill="none" stroke="#fff" stroke-width="2.6"/><line x1="15" y1="15" x2="22" y2="22" stroke="#fff" stroke-width="3" stroke-linecap="round"/></svg>
  </a>
  <nav class="nav">
    <a class="active" href="#" style="left:334px">Home</a>
    <a href="#" style="left:474px">The Way We Work</a>
    <a href="#" style="left:635px">What We Do</a>
    <a href="#" style="left:782px">Our Founder</a>
    <a href="#" style="left:917px">Insights</a>
    <a href="#" style="left:1034px">Contact</a>
  </nav>
</header>

<svg class="section-bg" style="top:615px" height="521" width="1200">
  <rect width="1200" height="521" fill="#f3f3f3"/>
  <path d="M520 0 C850 0 1160 120 1200 230 V0 Z" fill="#fff"/>
</svg>
<h2 class="title" style="left:133px;top:717px">The Way We Work</h2>
<p class="intro-text">Maecenas vel tortor accumsan quam varius imperdiet vel eget elit. Aenean facilisis tincidunt lectus, id dictum nisi luctus eget. Vivamus efficitur ex condimentum, malesuada eros eget, feugiat nibh. Sed tellus ex, imperdiet eget gravida sit amet, volutpat eget turpis. In nec ultricies est. Etiam mattis augue vehicula odio posuere.</p>
<ul class="intro-list">
  <li>Quisque aliquet ex nec est vestibulum pulvinar</li>
  <li>Pellentesque convallis molestie enim sit amet efficitur</li>
  <li>Etiam id imperdiet lectus</li>
  <li>Fusce vitae lectus sit amet mi pulvinar maximus</li>
</ul>
<a class="btn" href="#" style="left:133px;top:1003px;width:95px;height:36px">Read More</a>
<svg class="photo" style="left:746px;top:720px" width="321" height="320" role="img" aria-label="Photo of colleagues working at computers in a bright office">
  <defs><linearGradient id="officeTone" x1="0" y1="0" x2="0" y2="1"><stop offset="0" stop-color="#e8ecef"/><stop offset="1" stop-color="#9aa3ab"/></linearGradient></defs>
  <rect width="321" height="320" fill="url(#officeTone)"/>
</svg>

<h2 class="title center" style="top:1228px">What We Do</h2>

<div class="service" style="left:133px">
  <div class="service-icon">
    <svg width="62" height="62" viewBox="0 0 62 62" fill="none" stroke="#fff" stroke-width="2"><rect x="23" y="4" width="16" height="12"/><line x1="31" y1="16" x2="31" y2="30"/><line x1="10" y1="30" x2="52" y2="30"/><line x1="10" y1="30" x2="10" y2="42"/><line x1="31" y1="30" x2="31" y2="42"/><line x1="52" y1="30" x2="52" y2="42"/><circle cx="10" cy="49" r="7"/><circle cx="31" cy="49" r="7"/><circle cx="52" cy="49" r="7"/></svg>
  </div>
  <h3>Organisation<br>Design</h3>
  <p>Phasellus nisl est, condimentum vitae faucibus in, sollicitudin vel metus. Nunc sit amet consequat risus.</p>
  <a class="btn-ghost" href="#">Read More</a>
</div>

<div class="service" style="left:372px">
  <div class="service-icon">
    <svg width="64" height="62" viewBox="0 0 64 62" fill="none" stroke="#fff" stroke-width="2"><circle cx="12" cy="14" r="5"/><circle cx="32" cy="12" r="5"/><circle cx="52" cy="14" r="5"/><path d="M4 44 V26 h16 v18 M24 44 V24 h16 v20 M44 44 V26 h16 v18"/><line x1="2" y1="50" x2="62" y2="50"/></svg>
  </div>
  <h3>Employee<br>Experience</h3>
  <p>Phasellus nisl est, condimentum vitae faucibus in, sollicitudin vel metus. Nunc sit amet consequat risus.</p>
  <a class="btn-ghost" href="#">Read More</a>
</div>

<div class="service" style="left:611px">
  <div class="service-icon">
    <svg width="64" height="62" viewBox="0 0 64 62" fill="none" stroke="#fff" stroke-width="2"><circle cx="18" cy="14" r="6"/><circle cx="46" cy="34" r="6"/><path d="M6 42 c0-10 24-10 24 0 v6 H6z"/><path d="M34 58 c0-10 24-10 24 0"/><path d="M34 10 h12 v10 M42 16 l4 4 4-4"/><path d="M28 52 h-12 v-4"/></svg>
  </div>
  <h3>Change<br>Management</h3>
  <p>Phasellus nisl est, condimentum vitae faucibus in, sollicitudin vel metus. Nunc sit amet consequat risus.</p>
  <a class="btn-ghost" href="#">Read More</a>
</div>

<div class="service" style="left:850px">
  <div class="service-icon">
    <svg width="64" height="62" viewBox="0 0 64 62" fill="none" stroke="#fff" stroke-width="2"><rect x="22" y="6" width="36" height="26"/><line x1="28" y1="14" x2="40" y2="14"/><line x1="28" y1="20" x2="50" y2="20"/><line x1="28" y1="26" x2="44" y2="26"/><circle cx="12" cy="16" r="5"/><path d="M4 44 V26 h16 l6-6"/><circle cx="34" cy="42" r="4"/><circle cx="48" cy="42" r="4"/><path d="M28 56 v-8 h12 v8 M42 56 v-8 h12 v8"/></svg>
  </div>
  <h3>Executive<br>Coaching</h3>
  <p>Phasellus nisl est, condimentum vitae faucibus in, sollicitudin vel metus. Nunc sit amet consequat risus.</p>
  <a class="btn-ghost" href="#">Read More</a>
</div>

<svg class="section-bg" style="top:1694px" height="520" width="1200">
  <path d="M0 90 C400 90 900 60 1200 0 V520 H0 Z" fill="#f3f3f3"/>
</svg>
<svg class="photo" style="left:133px;top:1800px" width="321" height="321" role="img" aria-label="Portrait photo of the founder in a dark suit">
  <defs><linearGradient id="founderTone" x1="0" y1="0" x2="1" y2="0"><stop offset="0" stop-color="#8b7a68"/><stop offset="0.55" stop-color="#4a4a52"/><stop offset="1" stop-color="#d9dde0"/></linearGradient></defs>
  <rect width="321" height="321" fill="url(#founderTone)"/>
</svg>
<h2 class="title" style="right:133px;top:1797px">Our Founder</h2>
<div class="founder-name">Martin Hale, Founder</div>
<p class="founder-text">Aenean sed quam non sapien faucibus consequat vitae sit amet orci. Praesent quis risus mi. In mollis nulla in pulvinar dictum. Vivamus interdum sagittis felis, ut dapibus ligula feugiat ac. In dictum sapien eu tellus finibus fermentum. Aenean faucibus lacus ut mollis commodo. Donec vestibulum odio sem, ac laoreet massa ullamcorper id. Donec molestie nisl et tellus hendrerit vehicula. Nunc eu ligula sed quam pulvinar maximus in vitae eros. Proin porta fermentum ipsum, vel porttitor turpis venenatis luctus. Vivamus volutpat eu sapien quis tempus. Aenean feugiat viverra lorem ac sagittis.</p>
<a class="btn" href="#" style="left:972px;top:2081px;width:95px;height:40px">Read More</a>

<h2 class="title center" style="top:2309px">Insights</h2>
<div class="insight" style="left:133px"><span class="date">11 Apr, 2018</span><h3>Nullam accumsan purus vel tempus viverra</h3><p>Phasellus nisl est, condimentum vitae faucibus in, sollicitudin vel metus. Nunc sit amet consequat risus.</p><a class="btn-ghost" href="#">Read More</a></div>
<div class="insight" style="left:372px"><span class="date">11 Apr, 2018</span><h3>Nullam accumsan purus vel tempus viverra</h3><p>Phasellus nisl est, condimentum vitae faucibus in, sollicitudin vel metus. Nunc sit amet consequat risus.</p><a class="btn-ghost" href="#">Read More</a></div>
<div class="insight" style="left:611px"><span class="date">11 Apr, 2018</span><h3>Nullam accumsan purus vel tempus viverra</h3><p>Phasellus nisl est, condimentum vitae faucibus in, sollicitudin vel metus. Nunc sit amet consequat risus.</p><a class="btn-ghost" href="#">Read More</a></div>
<div class="insight" style="left:850px"><span class="date">11 Apr, 2018</span><h3>Nullam accumsan purus vel tempus viverra</h3><p>Phasellus nisl est, condimentum vitae faucibus in, sollicitudin vel metus. Nunc sit amet consequat risus.</p><a class="btn-ghost" href="#">Read More</a></div>

<svg class="section-bg" style="top:2680px" height="520" width="1200">
  <path d="M0 10 C300 -5 700 40 1000 220 C1100 290 1170 380 1200 440 V520 H0 Z" fill="#f3f3f3"/>
</svg>
<h2 class="title" style="left:133px;top:2813px">Contact Us</h2>
<div class="field" style="left:133px;top:2872px;width:201px">Name</div>
<div class="field" style="left:350px;top:2872px;width:199px">Company name</div>
<div class="field" style="left:133px;top:2927px;width:201px">Phone</div>
<div class="field" style="left:350px;top:2927px;width:199px">Email</div>
<div class="field" style="left:133px;top:2982px;width:416px">Message</div>
<a class="btn" href="#" style="left:133px;top:3040px;width:69px;height:38px">SEND</a>
<svg class="photo" style="left:746px;top:2790px" width="321" height="221" role="img" aria-label="Street map showing the office location">
  <defs><linearGradient id="mapTone" x1="0" y1="0" x2="1" y2="1"><stop offset="0" stop-color="#e4e4e4"/><stop offset="0.5" stop-color="#c9dcb4"/><stop offset="1" stop-color="#dcdcdc"/></linearGradient></defs>
  <rect width="321" height="221" fill="url(#mapTone)"/>
</svg>
<div class="map-info">18 Harbor Lane, Elmstead, 40218<br>Phone : 555 014 2290<br>Email : hello@bluefinch-example.com</div>

<svg class="section-bg" style="top:3188px" height="133" width="1200">
  <path d="M0 30 C400 -5 800 -5 1200 30 V133 H0 Z" fill="#2d2d2d"/>
</svg>
<div class="footer-links">Home<span>|</span>The Way We Work<span>|</span>What We Do<span>|</span>Our Founder<span>|</span>Insights<span>|</span>Contact</div>
<div class="copyright">Copyright © 2018 Bluefinch Advisory Partners. All rights reserved.</div>
<span class="social" style="left:1009px;background:#3b5998" aria-label="Social profile"></span>
<span class="social" style="left:1042px;background:#1da1f2" aria-label="Social profile"></span>

</body>
</html>
```